Plenth Vodka bottle label

I need a label designed for a vodka bottle. We are a small, farm based distillery producing hand crafted spirits. I've attached a mock-up of a wrap style label on the bottle we use. Logo is also attached. Would like to see it with some prominence at the top of the label. Thinking of a rock / music theme.

Target Market(s)

Adults of drinking age who enjoy quality spirits

Industry/Entity Type

Alcohol beverage production

Requirements
Must have
• Logo on top with Plenth vodka below. Alcohol details also needed: 750 mL 40% alc/vol
Nice to have
• predominantly a black and white label. Maybe a hit of color: copper, silver. Rock theme: guitar / vinyl album

```html
<!DOCTYPE html>
<html lang="en">
<head>
<meta charset="utf-8">
<title>Plenth Vodka – Label Set</title>
<link rel="stylesheet" href="https://fonts.googleapis.com/css2?family=Oswald:wght@400;500;700&family=Special+Elite&display=swap">
<style>
  :root {
    --ink: #0b0b0b;
    --paper: #ffffff;
    --copper: #c07a3e;
    --copper-soft: #8a5428;
    --silver: #d9d9d9;
  }
  * { margin: 0; padding: 0; box-sizing: border-box; }
  html, body { width: 831px; height: 1200px; overflow: hidden; background: var(--ink); }
  .canvas { position: relative; width: 831px; height: 1200px; background: var(--ink); font-family: "Oswald", sans-serif; color: var(--paper); }

  /* neck label */
  .neck-label { position: absolute; left: 215px; top: 150px; width: 400px; height: 78px; }
  .neck-label svg { position: absolute; inset: 0; }
  .neck-label .neck-side { position: absolute; top: 26px; width: 110px; font-size: 10px; letter-spacing: 1.5px; line-height: 1.3; color: var(--copper); text-align: center; }
  .neck-label .neck-left { left: 22px; }
  .neck-label .neck-right { right: 22px; }
  .neck-label .brand-mark { position: absolute; left: 0; right: 0; top: 18px; text-align: center; font-size: 28px; font-weight: 500; color: var(--paper); }

  /* shared label frame */
  .label { position: absolute; top: 300px; width: 345px; height: 560px; }
  .label > svg.frame { position: absolute; inset: 0; }
  .label-body { position: absolute; inset: 40px 34px; display: flex; flex-direction: column; align-items: center; text-align: center; }

  .front-label { left: 48px; }
  .back-label { left: 438px; }

  .brand-mark { font-family: "Oswald", sans-serif; font-weight: 500; font-size: 36px; color: var(--paper); letter-spacing: 1px; }
  .grain-line { margin-top: 14px; font-size: 17px; font-weight: 700; letter-spacing: 3px; color: var(--copper); }
  .product-name { margin-top: 10px; font-size: 92px; font-weight: 700; line-height: 0.95; letter-spacing: 2px; color: var(--ink); -webkit-text-stroke: 2px var(--paper); text-transform: uppercase; }
  .product-type { margin-top: 16px; font-size: 17px; letter-spacing: 3px; color: var(--paper); border-top: 1px solid var(--copper); border-bottom: 1px solid var(--copper); padding: 4px 10px; }
  .flourish { margin-top: 22px; width: 220px; height: 70px; background: linear-gradient(180deg, var(--copper) 0%, var(--copper-soft) 100%); opacity: 0.75; border-radius: 4px; }
  .volume-row { margin-top: 18px; width: 100%; display: flex; justify-content: space-between; font-size: 13px; letter-spacing: 1px; color: var(--silver); }

  .origin-line { margin-top: 10px; font-size: 17px; font-weight: 700; letter-spacing: 2px; color: var(--copper); border-bottom: 1px solid var(--copper); padding-bottom: 8px; width: 100%; }
  .story { margin-top: 26px; font-family: "Special Elite", monospace; font-size: 17px; line-height: 1.45; color: var(--paper); text-transform: uppercase; }
  .caution-box { margin-top: 30px; width: 100%; border: 1px solid var(--copper); padding: 10px 12px; text-align: left; font-size: 10px; line-height: 1.45; color: var(--silver); }
  .caution-box strong { display: block; font-size: 12px; color: var(--copper); margin-bottom: 4px; font-weight: 500; }
  .back-volume { margin-top: auto; font-size: 12px; letter-spacing: 1px; color: var(--silver); }
</style>
</head>
<body>
<main class="canvas">

  <section class="neck-label">
    <svg viewBox="0 0 400 78" width="400" height="78">
      <polygon points="14,0 386,0 400,14 400,64 386,78 14,78 0,64 0,14" fill="#0b0b0b" stroke="#c07a3e" stroke-width="2"/>
      <polygon points="18,5 382,5 395,18 395,60 382,73 18,73 5,60 5,18" fill="none" stroke="#8a5428" stroke-width="1"/>
      <line x1="140" y1="39" x2="120" y2="39" stroke="#c07a3e"/>
      <line x1="260" y1="39" x2="280" y2="39" stroke="#c07a3e"/>
    </svg>
    <div class="neck-side neck-left">HANDCRAFTED<br>VODKA</div>
    <div class="brand-mark">Harlow</div>
    <div class="neck-side neck-right">750 mL<br>40% ALC/VOL</div>
  </section>

  <section class="label front-label">
    <svg class="frame" viewBox="0 0 345 560" width="345" height="560">
      <polygon points="30,0 150,0 172,-0 195,0 315,0 345,30 345,530 315,560 30,560 0,530 0,30" fill="#0b0b0b" stroke="#c07a3e" stroke-width="2.5"/>
      <polygon points="34,9 311,9 336,34 336,526 311,551 34,551 9,526 9,34" fill="none" stroke="#8a5428" stroke-width="1.2"/>
    </svg>
    <div class="label-body">
      <div class="brand-mark">Harlow</div>
      <div class="grain-line">100% PURE GRAIN</div>
      <h1 class="product-name">Plenth<br>Vodka</h1>
      <div class="product-type">HANDCRAFTED VODKA</div>
      <div class="flourish" role="img" aria-label="Copper scrollwork ornament"></div>
      <div class="volume-row"><span>750 mL</span><span>40% alc/vol</span></div>
    </div>
  </section>

  <section class="label back-label">
    <svg class="frame" viewBox="0 0 345 560" width="345" height="560">
      <polygon points="30,0 315,0 345,30 345,530 315,560 30,560 0,530 0,30" fill="#0b0b0b" stroke="#c07a3e" stroke-width="2.5"/>
      <polygon points="34,9 311,9 336,34 336,526 311,551 34,551 9,526 9,34" fill="none" stroke="#8a5428" stroke-width="1.2"/>
    </svg>
    <div class="label-body">
      <div class="origin-line">HANDCRAFTED IN ONTARIO</div>
      <p class="story">Distilling is a proud tradition of Stonemere. We are third generation distillers. Second generation legally.</p>
      <div class="caution-box">
        <strong>Caution:</strong>
        Do not drink if pregnant. Alcohol impairs the ability to drive a car or operate machinery. Enjoy responsibly.
      </div>
      <div class="back-volume">750 mL · 40% alc/vol</div>
    </div>
  </section>

</main>
</body>
</html>
```